Website for new dental office

I am Dr. Colin Ashford and am building a new dental practice. I specialize in general dentistry. I am young and have a higher end dental practice incorporating very new technologies and would like my website to reflect that. As many dental patients are older, the website must be very easy to navigate. I would like patients to be able to request appointments, and will eventually add on patient information forms (the health history, etc, that you normally fill out in the practice) from my practice management software, so leave an area for that.

Industry/Entity Type

Building

```html
<!DOCTYPE html>
<html lang="en">
<head>
<meta charset="utf-8">
<title>Colin Ashford, DDS – Case Studies</title>
<link href="https://fonts.googleapis.com/css2?family=Open+Sans:wght@300;400;600;700&display=swap" rel="stylesheet">
<style>
:root{
  --blue:#1f86d6;
  --blue-dark:#1a5ea6;
  --nav-top:#3b97e6;
  --nav-bottom:#1c6fc8;
  --nav-active:#134f96;
  --text:#333;
  --muted:#666;
  --orange:#f7891e;
  --panel:#f6f6f6;
}
*{margin:0;padding:0;box-sizing:border-box}
html,body{width:1067px;height:1200px;overflow:hidden;background:#fff}
body{position:relative;font-family:"Open Sans",Arial,sans-serif;color:var(--text)}
.site-header{position:absolute;left:0;top:0;width:1067px;height:104px;background:linear-gradient(#dcedfc,#fff)}
.brand{position:absolute;left:96px;top:36px;font-size:30px;font-weight:600;color:var(--blue);font-variant:small-caps;letter-spacing:.5px}
.phone{position:absolute;right:107px;top:34px;display:flex;align-items:center;gap:10px;font-size:24px;color:#444}
.main-nav{position:absolute;left:0;top:104px;width:1067px;height:39px;background:linear-gradient(var(--nav-top),var(--nav-bottom))}
.main-nav a{position:absolute;top:0;height:39px;line-height:39px;color:#fff;font-size:14px;text-decoration:none}
.main-nav a.sep{border-left:1px solid rgba(255,255,255,.2)}
.main-nav .home{font-weight:700}
.main-nav .active{background:var(--nav-active);text-align:center}
.hero{position:absolute;left:0;top:143px;width:1067px;height:225px;background:linear-gradient(90deg,#cfdde9 0%,#eef4fa 35%,#fff 70%);border-bottom:1px solid #d7e6f2}
.hero h1{position:absolute;left:96px;top:52px;font-size:50px;font-weight:300;color:var(--blue-dark);line-height:1}
.hero h1 b{font-weight:700}
.hero p{position:absolute;left:96px;top:122px;width:440px;font-size:18.5px;line-height:24px;color:#333}
.hero-art{position:absolute;left:631px;top:8px;width:396px;height:217px;border-radius:40px 40px 0 0;background:radial-gradient(circle at 80% 70%,#d9101a 0 18%,transparent 19%),linear-gradient(#f4f4f4,#dcdcdc)}
.section-title{position:absolute;left:93px;top:403px;font-size:21px;font-weight:300;color:var(--blue)}
.rule{position:absolute;left:230px;top:416px;width:721px;height:3px;border-top:1px dotted #bbb}
.rule::before{content:"";position:absolute;left:0;top:-2px;width:178px;height:3px;background:var(--blue)}
.case{position:absolute;width:392px}
.case .photo{height:123px}
.case h2{margin-top:14px;font-size:18px;font-weight:600;color:var(--blue)}
.case p{margin-top:12px;font-size:11.5px;line-height:15.3px;color:var(--muted)}
.cta{position:absolute;left:96px;top:1050px;width:854px;height:86px;background:var(--panel);border:1px solid #e6e6e6;border-radius:8px}
.cta h3{position:absolute;left:23px;top:28px;font-size:22px;font-weight:600;color:#555}
.cta a{position:absolute;left:655px;top:18px;width:176px;height:48px;background:linear-gradient(#fa9a2c,var(--orange));border-radius:3px;color:#fff;text-decoration:none;font-size:16px;font-weight:600;line-height:48px;padding-left:8px}
.cta a svg{position:absolute;right:10px;top:13px}
.footer{position:absolute;left:0;top:1163px;width:1067px;text-align:center;font-size:11.5px;color:#222}
</style>
</head>
<body>
<header class="site-header">
  <div class="brand">Colin Ashford, DDS</div>
  <div class="phone">
    <svg width="36" height="36" viewBox="0 0 36 36"><circle cx="21" cy="15" r="12" fill="none" stroke="#1f86d6" stroke-width="2.5"/><text x="21" y="20" font-size="12" font-weight="700" fill="#1f86d6" text-anchor="middle" font-family="Open Sans,sans-serif">24</text><path d="M4 6 l6 -2 4 8 -4 3 q3 7 10 11 l3 -4 8 4 -2 6 q-12 2 -22 -10 q-6 -8 -3 -16z" fill="#333"/></svg>
    <span>+123 555 0188</span>
  </div>
</header>
<nav class="main-nav">
  <a class="home" style="left:97px">HOME</a>
  <a style="left:197px">ABOUT US</a>
  <a class="sep" style="left:287px;padding-left:30px">SERVICES</a>
  <a class="sep" style="left:403px;padding-left:28px">RESOURCES</a>
  <a class="sep" style="left:532px;padding-left:29px">GALLERY</a>
  <a class="active" style="left:644px;width:93px">CASES</a>
  <a style="left:766px">TEAM</a>
  <a class="sep" style="left:832px;padding-left:26px">CONTACT</a>
</nav>
<section class="hero">
  <h1>Case <b>Studies</b></h1>
  <p>Lorem Ipsum is simply dummy text of the printing and typesetting industry. Lorem Ipsum has been</p>
  <div class="hero-art" role="img" aria-label="3D tooth beside a white figure holding a red first aid kit"></div>
</section>
<h2 class="section-title">Case Studies</h2>
<div class="rule"></div>

<article class="case" style="left:98px;top:461px">
  <div class="photo" role="img" aria-label="Smiling woman biting a green apple" style="background:linear-gradient(90deg,#4e6a3c,#8a7a5e 55%,#c9a58c)"></div>
  <h2>Cosmetics</h2>
  <p>Lorem Ipsum is simply dummy text of the printing and typesetting industry. Lorem Ipsum has been the industry's standard dummy text ever since the 1500s, Lorem Ipsum is simply dummy text of the printing and typesetting industry. Lorem Ipsum has been the industry's standard dummy text ever since the 1500s,</p>
</article>
<article class="case" style="left:567px;top:461px">
  <div class="photo" role="img" aria-label="Model of a dental implant between teeth" style="background:linear-gradient(90deg,#6d4a2a,#a9843f 40%,#cfd6da 70%,#e3e7ea)"></div>
  <h2>Restorative</h2>
  <p>Lorem Ipsum is simply dummy text of the printing and typesetting industry. Lorem Ipsum has been the industry's standard dummy text ever since the 1500s, Lorem Ipsum is simply dummy text of the printing and typesetting industry. Lorem Ipsum has been the industry's standard dummy text ever since the 1500s,</p>
</article>
<article class="case" style="left:96px;top:735px">
  <div class="photo" role="img" aria-label="Close view of a bright white smile" style="background:linear-gradient(90deg,#e9c6b6,#f3e2dc 40%,#e6efdc 75%,#f3f7ef)"></div>
  <h2>Cosmetics</h2>
  <p>Lorem Ipsum is simply dummy text of the printing and typesetting industry. Lorem Ipsum has been the industry's standard dummy text ever since the 1500s, Lorem Ipsum is simply dummy text of the printing and typesetting industry. Lorem Ipsum has been the industry's standard dummy text ever since the 1500s,</p>
</article>
<article class="case" style="left:565px;top:735px">
  <div class="photo" role="img" aria-label="Two panoramic dental X-rays before and after treatment" style="background:radial-gradient(ellipse at 25% 50%,#9a9a9a,#2a2a2a 70%),#222;background:linear-gradient(90deg,#3a3a3a,#8e8e8e 25%,#3a3a3a 49.5%,#fff 49.5%,#fff 50%,#3a3a3a 50%,#8e8e8e 75%,#3a3a3a)"></div>
  <h2>Restorative</h2>
  <p>Lorem Ipsum is simply dummy text of the printing and typesetting industry. Lorem Ipsum has been the industry's standard dummy text ever since the 1500s, Lorem Ipsum is simply dummy text of the printing and typesetting industry. Lorem Ipsum has been the industry's standard dummy text ever since the 1500s,</p>
</article>

<section class="cta">
  <h3>Want to Get Treated? Schedule Your Appointment Now!</h3>
  <a>Get Appointment
    <svg width="22" height="22" viewBox="0 0 22 22" fill="none" stroke="#5a2d00" stroke-width="1.5"><rect x="2" y="4" width="18" height="16" rx="1"/><line x1="2" y1="8" x2="20" y2="8"/><line x1="7" y1="2" x2="7" y2="6"/><line x1="15" y1="2" x2="15" y2="6"/><path d="M6 11h2M10 11h2M14 11h2M6 14h2M10 14h2M14 14h2M6 17h2M10 17h2"/></svg>
  </a>
</section>
<footer class="footer">© Copyrights 2014 All rights Reserved</footer>
</body>
</html>
```